KRWB new business card design

We need a business card design for our established business which is Australia wide however based in Melbourne. We are a young team of Financial Planners who specialize in Insurance and Basic super advice for people like us.

We are people who help our clients get things done in a timely and cost effective manner whilst having a good time and a laugh along the way.

We would like this to have a consistent feel with our new e-brochure which i have attached from a color and font perspective.

Industry/Entity Type

Business

Requirements
Must have
• We do not need specific address details rather just the states we are in:

VIC/NSW/QLD/TAS
Nice to have
• Curved edge to mate the brochure

```html
<!DOCTYPE html>
<html lang="en">
<head>
<meta charset="utf-8">
<title>KRWB business card concepts</title>
<link rel="stylesheet" href="https://fonts.googleapis.com/css2?family=Arimo:ital,wght@0,400;0,700;1,700&family=Open+Sans:wght@400;600&display=swap">
<style>
  :root {
    --stage: #6e4a2d;
    --ink-dark: #111213;
    --ink-mid: #1c1d1f;
    --white: #ffffff;
    --green: #6cc04a;
    --green-deep: #1fa34a;
    --grey-text: #6d6e71;
    --grey-dark: #3a3b3d;
    --label: #1a1a1a;
  }
  * { box-sizing: border-box; margin: 0; padding: 0; }
  html, body { width: 1200px; height: 788px; overflow: hidden; }
  body {
    position: relative;
    background: var(--stage);
    font-family: "Arimo", Arial, sans-serif;
  }

  .view-label {
    position: absolute;
    width: 525px;
    text-align: center;
    font-family: "Open Sans", Arial, sans-serif;
    font-size: 21px;
    color: var(--label);
  }

  .card {
    position: absolute;
    width: 525px;
    height: 299px;
    border-radius: 20px;
    overflow: hidden;
    box-shadow: 0 4px 12px rgba(0,0,0,.45);
  }
  .card--front { left: 53px; top: 75px; background: radial-gradient(circle at 50% 30%, #2f3033 0%, var(--ink-mid) 45%, var(--ink-dark) 100%); }
  .card--back1 { left: 622px; top: 75px; background: var(--white); }
  .card--back2 { left: 53px; top: 446px; background: var(--white); }
  .card--back3 { left: 622px; top: 446px; background: linear-gradient(160deg, #2b2c2e 0%, #151617 60%, #0d0d0e 100%); }

  /* brand name lockup */
  .brand { position: absolute; display: flex; align-items: center; gap: 10px; }
  .brand__mark { background: var(--green); flex: none; }
  .brand__name { font-weight: 700; letter-spacing: 1px; white-space: nowrap; }

  .card--front .brand { left: 0; right: 0; top: 40px; justify-content: center; }
  .card--front .brand__mark { width: 60px; height: 60px; }
  .card--front .brand__name { color: var(--white); font-size: 44px; }

  /* front band */
  .contact-band {
    position: absolute; left: 0; right: 0; top: 173px; height: 70px;
    background: var(--green);
    border-top: 3px solid var(--ink-dark);
    border-bottom: 3px solid var(--ink-dark);
    box-shadow: 0 -2px 0 var(--green-deep), 0 2px 0 var(--green-deep);
  }
  .adviser { position: absolute; left: 82px; top: 5px; color: var(--white); font-weight: 700; }
  .adviser__name { font-size: 18px; line-height: 22px; }
  .adviser__role { font-size: 13px; line-height: 17px; }
  .phones { position: absolute; right: 83px; top: 7px; text-align: right; color: var(--white); font-size: 13.5px; line-height: 17px; }
  .phones em { font-style: italic; font-weight: 700; margin-right: 4px; }

  .web-line, .states {
    position: absolute; left: 0; right: 0; text-align: center;
    font-family: "Open Sans", Arial, sans-serif; color: var(--white); font-size: 13px;
  }
  .web-line { top: 249px; }
  .web-line em { font-style: italic; font-weight: 600; margin-right: 3px; }
  .web-line .sep { margin: 0 8px; }
  .states { top: 271px; }

  /* specialities list */
  .specialities { position: absolute; font-weight: 700; }
  .specialities__title { font-style: italic; font-size: 18px; margin-bottom: 8px; }
  .specialities__item { font-size: 14px; line-height: 34px; display: flex; align-items: center; }
  .specialities__item::before { content: ""; width: 4px; height: 4px; margin-right: 6px; background: currentColor; }

  .card--back1 .brand { left: 72px; top: 122px; }
  .card--back1 .brand__mark { width: 44px; height: 44px; }
  .card--back1 .brand__name { color: var(--ink-dark); font-size: 34px; }
  .divider {
    position: absolute; left: 260px; top: 20px; width: 2px; height: 235px;
    background: linear-gradient(to bottom, rgba(0,0,0,0), #8a8b8d 50%, rgba(0,0,0,0));
  }
  .card--back1 .specialities { left: 319px; top: 45px; color: var(--grey-text); }
  .tagline-band {
    position: absolute; left: 0; right: 0; bottom: 0; height: 39px;
    background: var(--green); color: var(--white);
    font-weight: 700; font-size: 14px; text-align: center; line-height: 39px;
  }

  .card--back2 .specialities { left: 0; right: 0; top: 46px; color: var(--grey-dark); text-align: center; }
  .card--back2 .specialities__item { justify-content: center; }
  .card--back2 .tagline { position: absolute; left: 0; right: 0; top: 268px; text-align: center; color: var(--grey-dark); font-weight: 700; font-size: 14px; }

  .card--back3 .brand { left: 62px; top: 118px; }
  .card--back3 .brand__mark { width: 56px; height: 56px; }
  .card--back3 .brand__name { color: var(--white); font-size: 52px; }
  .card--back3 .specialities { left: 314px; top: 24px; color: var(--white); }
  .card--back3 .specialities__title { font-size: 19px; }
  .card--back3 .tagline { position: absolute; left: 313px; top: 253px; color: var(--green); font-weight: 700; font-size: 14px; line-height: 18px; }
</style>
</head>
<body>

  <div class="view-label" style="left:53px; top:33px;">Front</div>
  <div class="view-label" style="left:622px; top:33px;">Back - 1</div>
  <div class="view-label" style="left:53px; top:402px;">Back - 2</div>
  <div class="view-label" style="left:622px; top:402px;">Back - 3</div>

  <section class="card card--front">
    <div class="brand"><span class="brand__mark"></span><span class="brand__name">KRWB</span></div>
    <div class="contact-band">
      <div class="adviser">
        <div class="adviser__name">Daniel Hartwell</div>
        <div class="adviser__role">DipFP, BCom, RG146</div>
        <div class="adviser__role">Financial Adviser</div>
      </div>
      <div class="phones">
        <div><em>cell</em>0400 555 218</div>
        <div><em>phone</em>1300 555 406</div>
        <div><em>fax</em>03 9555 0147</div>
      </div>
    </div>
    <div class="web-line"><em>email</em>daniel@krwb.com.au<span class="sep">|</span><em>web</em>www.krwb.com.au</div>
    <div class="states">VIC/NSW/QLD/TAS</div>
  </section>

  <section class="card card--back1">
    <div class="brand"><span class="brand__mark"></span><span class="brand__name">KRWB</span></div>
    <div class="divider"></div>
    <div class="specialities">
      <div class="specialities__title">Specialising in</div>
      <div class="specialities__item">Risk Insurance</div>
      <div class="specialities__item">Debt Management</div>
      <div class="specialities__item">Superannuation</div>
      <div class="specialities__item">Wealth Creation</div>
      <div class="specialities__item">Retirement Planning</div>
    </div>
    <div class="tagline-band">CLEAR GOALS, CONFIDENT TOMORROW</div>
  </section>

  <section class="card card--back2">
    <div class="specialities">
      <div class="specialities__title">Specialising in</div>
      <div class="specialities__item">Risk Insurance</div>
      <div class="specialities__item">Debt Management</div>
      <div class="specialities__item">Superannuation</div>
      <div class="specialities__item">Wealth Creation</div>
      <div class="specialities__item">Retirement Planning</div>
    </div>
    <div class="tagline">CLEAR GOALS, CONFIDENT TOMORROW</div>
  </section>

  <section class="card card--back3">
    <div class="brand"><span class="brand__mark"></span><span class="brand__name">KRWB</span></div>
    <div class="specialities">
      <div class="specialities__title">Specialising in</div>
      <div class="specialities__item">Risk Insurance</div>
      <div class="specialities__item">Debt Management</div>
      <div class="specialities__item">Superannuation</div>
      <div class="specialities__item">Wealth Creation</div>
      <div class="specialities__item">Retirement Planning</div>
    </div>
    <div class="tagline">CLEAR GOALS<br>CONFIDENT TOMORROW</div>
  </section>

</body>
</html>
```